Business Card for premium dental clinic

We are a premium dental clinic based in Brasov, Romania with more than 15 year on the market, providing quality dental treatment made by a team of more specialized dentists, working with modern equipment as a solution to beautiful and healthy teeth.

Our current logo for the clinic use 2 square with colors black and gold - dr Ternisu - studio, using family fonts Bodoni, Myriad Pro and Segoe Print.
Depending on the printing we used some gold CMYK background or gold foil picture background or a gold gradient.
We want a business card:
- eye catching business card
- distinguished business card
- premium design
- to keep the color scheme of black and gold
- to attract the customers to spent time reading the information
- modern concept

```html
<!DOCTYPE html>
<html lang="en">
<head>
<meta charset="utf-8">
<title>dr Ternisu – Business Card</title>
<link href="https://fonts.googleapis.com/css2?family=Montserrat:wght@500;700&display=swap" rel="stylesheet">
<style>
  :root {
    --backdrop: #3a302c;
    --card-black: #141414;
    --gold: #f2c52b;
    --gold-deep: #c8961a;
    --white: #ffffff;
  }
  * { box-sizing: border-box; margin: 0; padding: 0; }
  html, body { width: 1200px; height: 716px; overflow: hidden; }
  body {
    background: var(--backdrop);
    font-family: "Montserrat", sans-serif;
    display: flex;
    align-items: center;
    justify-content: center;
    gap: 48px;
  }
  .card {
    width: 540px;
    height: 308px;
    background: var(--card-black);
    border-radius: 6px;
    position: relative;
    display: flex;
    align-items: center;
  }
  .card--front { justify-content: center; }
  .brand {
    display: flex;
    align-items: center;
    gap: 12px;
    color: var(--white);
    font-weight: 500;
    font-size: 26px;
    letter-spacing: 0.5px;
  }
  .brand__square {
    width: 34px;
    height: 34px;
    background: linear-gradient(135deg, var(--gold), var(--gold-deep));
  }
  .card--back { padding: 0 34px; }
  .card--back .brand { font-size: 22px; }
  .card--back .brand__square { width: 28px; height: 28px; }
  .divider {
    width: 2px;
    height: 150px;
    background: var(--gold);
    margin: 0 26px;
  }
  .contact { color: var(--white); font-size: 13px; line-height: 1.55; }
  .contact__name {
    color: var(--gold);
    font-weight: 700;
    font-size: 24px;
    letter-spacing: 1px;
    margin-bottom: 8px;
  }
  .contact__row { display: flex; align-items: center; gap: 8px; }
  .contact__row svg { width: 11px; height: 11px; flex: none; }
  .contact__address { margin-top: 4px; }
</style>
</head>
<body>
  <section class="card card--front">
    <div class="brand"><span class="brand__square"></span>dr Ternisu</div>
  </section>

  <section class="card card--back">
    <div class="brand"><span class="brand__square"></span>dr Ternisu</div>
    <div class="divider"></div>
    <div class="contact">
      <h1 class="contact__name">DR TERNISU</h1>
      <p class="contact__row">
        <svg viewBox="0 0 12 12"><path d="M2 1h2.5l1 3-1.5 1a6 6 0 0 0 3 3l1-1.5 3 1V10a1 1 0 0 1-1 1A9 9 0 0 1 1 2a1 1 0 0 1 1-1z" fill="var(--gold)"/></svg>
        +40 268 555 019
      </p>
      <p class="contact__row">
        <svg viewBox="0 0 12 12"><rect x="1" y="2.5" width="10" height="7" fill="none" stroke="var(--gold)" stroke-width="1.2"/><path d="M1 2.5l5 4 5-4" fill="none" stroke="var(--gold)" stroke-width="1.2"/></svg>
        info@drternisu.ro
      </p>
      <p class="contact__row">
        <svg viewBox="0 0 12 12"><circle cx="6" cy="6" r="5" fill="none" stroke="var(--gold)" stroke-width="1.2"/><path d="M1 6h10M6 1c-2.5 3-2.5 7 0 10M6 1c2.5 3 2.5 7 0 10" fill="none" stroke="var(--gold)" stroke-width="1"/></svg>
        www.drternisu.ro
      </p>
      <p class="contact__address">Strada Lungă 48,<br>Brașov 500099, Romania</p>
    </div>
  </section>
</body>
</html>
```